Informational Site for Advanced Chemistry R&D

The company develops oxidation chemistry for air, water, fuel pollution controls. The site has been prototyped at www.velquaresearch.example. Take a look. Now, the task is to design it for eye-catching beauty with use of color, on-page scroll-driven color transition and parallax effects. Should capture the themes: high technology, wow it's beautiful, modern, uncluttered, clean urban environment.

Target Market(s)

China Environmentally Conscious Government and Industry,

Industry/Entity Type

It Company

Number of Pages Required

3 page

Font styles to use
Sans Serif

Requirements
Must have
• Parallax effects, desktop compatible, Rich, Modern, Simple, Graphic
Nice to have
• Mobile Phone Compatible
Should not have
• Flash, or anything that is slow to load or requires high bandwidth

```html
<!DOCTYPE html>
<html lang="en">
<head>
<meta charset="utf-8">
<title>Velqua Research — Advanced Oxidation</title>
<link rel="stylesheet" href="https://fonts.googleapis.com/css2?family=Raleway:wght@400;500;600&family=Open+Sans:wght@400;600&display=swap">
<style>
:root{
  --blue:#1b75bb;
  --blue-deep:#1a6aa8;
  --teal:#2aa9b5;
  --green:#5bb045;
  --orange:#f39b13;
  --sky:#1e93d2;
  --navy:#164f7e;
  --ink:#222;
  --grey:#7a7a7a;
  --light:#e6e6e6;
  --white:#fff;
}
*{margin:0;padding:0;box-sizing:border-box}
html,body{width:1200px;height:2812px;overflow:hidden}
body{position:relative;background:var(--white);font-family:"Open Sans",Arial,sans-serif;color:var(--ink)}
.abs{position:absolute}
.center{text-align:center}

/* header */
.site-header{left:0;top:0;width:1200px;height:97px;background:var(--white)}
.brand{left:176px;top:24px;display:flex;align-items:center;gap:12px}
.brand-dot{width:40px;height:40px;border-radius:50%;background:var(--blue)}
.brand-name{font-family:"Raleway",sans-serif;font-weight:600;font-size:34px;color:var(--blue)}
.main-nav{left:548px;top:54px;display:flex;gap:0;font-family:"Raleway",sans-serif;font-weight:600;font-size:15px;color:var(--blue)}
.main-nav a{display:block;text-decoration:none;color:inherit;margin-right:60px;letter-spacing:.3px}
.main-nav a.active{border-bottom:2px solid var(--blue);padding-bottom:14px}

/* hero */
.hero{left:0;top:97px;width:1200px;height:488px;background:linear-gradient(100deg,#eef3f7 0%,#dfe8ef 45%,#cfe6ef 75%,#bcdde9 100%)}
.hero-title{left:276px;top:262px;width:677px;height:68px;background:rgba(27,130,190,.85);color:var(--white);font-family:"Raleway",sans-serif;font-size:40px;line-height:68px}
.hero-sub{left:276px;top:330px;width:677px;height:51px;background:var(--green);color:var(--white);font-family:"Raleway",sans-serif;font-weight:500;font-size:20px;line-height:51px}
.slider-dots{left:558px;top:549px;display:flex;gap:4px}
.slider-dots span{width:17px;height:17px;border-radius:50%;background:var(--white);border:1px solid #ccc}
.slider-dots span.on{background:#d9b310}

/* intro */
.intro-title{left:0;top:633px;width:1200px;font-family:"Raleway",sans-serif;font-size:31px;color:var(--blue)}
.intro-lead{left:0;top:684px;width:1200px;font-size:15px;color:#444}
.intro-body{left:250px;top:718px;width:700px;font-size:11px;line-height:19px;color:var(--grey)}
.domain-line{left:338px;top:837px;width:530px;height:2px;background:var(--light)}
.domain{width:220px;text-align:center}
.domain-ring{width:108px;height:108px;border-radius:50%;border:3px solid var(--light);background:var(--white);margin:0 auto;display:flex;align-items:center;justify-content:center}
.domain-disc{width:92px;height:92px;border-radius:50%;display:flex;align-items:center;justify-content:center}
.domain-name{margin-top:18px;font-family:"Raleway",sans-serif;font-size:16px;font-weight:500;color:#333}
.domain-text{margin-top:4px;font-size:11px;line-height:19px;color:var(--grey)}
.section-rule{left:0;top:1029px;width:1200px;height:1px;background:var(--light)}

/* advanced oxidation */
.ao-text{left:182px;top:1110px;width:410px}
.ao-text h2{font-family:"Raleway",sans-serif;font-weight:400;font-size:31px;color:#111;margin-bottom:14px}
.ao-text p{font-size:11px;line-height:18px;color:#555}
.ao-list{list-style:none;margin:14px 0 22px}
.ao-list li{display:flex;align-items:center;gap:8px;font-size:11px;color:#333;margin-bottom:9px}
.tick{width:13px;height:13px;border-radius:50%;background:var(--teal);display:flex;align-items:center;justify-content:center}
.ao-visual{left:600px;top:1029px;width:600px;height:392px;background:radial-gradient(circle at 55% 50%,#e9f1f8 0%,#b9cfe2 55%,#8eb2d1 100%)}

/* solutions */
.tile{width:600px;height:285px;color:var(--white);text-align:center}
.tile-fuel{left:0;top:1421px;background:linear-gradient(135deg,#4f9f35,#6cbb4a)}
.tile-voc{left:600px;top:1421px;background:linear-gradient(135deg,#f6a519,#ee8d0c)}
.tile-flue{left:0;top:1706px;background:linear-gradient(135deg,#2b9fdc,#1a7fc2)}
.tile-water{left:600px;top:1706px;background:linear-gradient(135deg,#1d6eae,#144f86)}
.tile-icon{margin:62px auto 0;width:60px;height:70px}
.tile h3{font-family:"Raleway",sans-serif;font-weight:400;font-size:22px;margin-top:10px}
.tile p{font-size:10.5px;line-height:17px;width:440px;margin:6px auto 0;opacity:.95}
.read-more{display:inline-block;margin-top:14px;border:1px solid var(--white);font-size:9px;padding:6px 18px;letter-spacing:.5px}
.solution-badge{left:546px;top:1652px;width:108px;height:108px;border-radius:50%;background:var(--white);border:5px solid #e2e2e2;display:flex;align-items:center;justify-content:center;text-align:center;font-family:"Raleway",sans-serif;font-size:14px;line-height:17px;color:#444}

/* partners */
.partners-title{left:0;top:2052px;width:1200px;font-family:"Raleway",sans-serif;font-size:23px;color:var(--blue)}
.partner{width:200px;text-align:center}
.partner-mark{height:96px;display:flex;align-items:center;justify-content:center}
.partner-name{font-family:"Raleway",sans-serif;font-weight:600;font-size:17px;color:var(--blue)}
.partner-role{margin-top:10px;font-size:11px;line-height:18px;color:#999}

/* contact */
.contact{left:0;top:2385px;width:1200px;height:427px;background:var(--blue)}
.contact-map{left:170px;top:2470px;width:860px;height:320px;background:radial-gradient(ellipse at center,rgba(255,255,255,.07),rgba(255,255,255,0) 70%)}
.contact-title{left:0;top:2428px;width:1200px;font-family:"Raleway",sans-serif;font-size:28px;color:var(--white)}
.contact-rule{left:558px;top:2470px;width:84px;height:2px;background:var(--white)}
.field{left:182px;width:337px;background:var(--white);font-size:10px;color:#999;padding:8px 14px}
.send{left:182px;top:2670px;width:82px;height:30px;background:#0f3a60;color:var(--white);font-size:12px;font-weight:600;line-height:30px;text-align:center}
.contact-info{left:611px;top:2504px;color:var(--white);font-size:13px;line-height:26px}
.contact-info .row{display:flex;align-items:center;gap:8px}
.social{left:611px;top:2626px;display:flex;gap:6px}
.social span{width:27px;height:27px;border-radius:50%;border:2px solid var(--white)}
.footer-note{left:182px;top:2776px;font-size:10px;color:rgba(255,255,255,.75)}
.footer-rule{left:0;top:2762px;width:1200px;height:1px;background:rgba(255,255,255,.15)}
</style>
</head>
<body>

<header class="abs site-header">
  <div class="abs brand"><span class="brand-dot"></span><span class="brand-name">Velqua Research</span></div>
  <nav class="abs main-nav">
    <a class="active" href="#">HOME</a><a href="#">TECHNOLOGY</a><a href="#">PRODUCTS</a><a href="#">CONTACT</a>
  </nav>
</header>

<section class="abs hero" role="img" aria-label="Two scientists in lab coats working at a microscope in a bright laboratory"></section>
<div class="abs hero-title center">ADVANCED OXIDATION</div>
<div class="abs hero-sub center">SCIENCE FOR ENVIRONMENTAL POLLUTION MANAGEMENT</div>
<div class="abs slider-dots"><span class="on"></span><span></span><span></span><span></span></div>

<h1 class="abs intro-title center" style="font-weight:400">NEW IDEAS FOR A CLEANER WORLD</h1>
<p class="abs intro-lead center">Environmental pollution control solutions employing nature's most reactive Free Radical</p>
<p class="abs intro-body center">Our team turns the hydroxyl radical into a practical tool for industry, removing sulfur, organics and odours from fuel, air and water streams. Each process runs at low temperature and pressure, uses little energy and leaves only harmless end products behind.</p>

<div class="abs domain-line"></div>
<div class="abs domain" style="left:228px;top:784px">
  <div class="domain-ring"><div class="domain-disc" style="background:var(--sky)">
    <svg width="30" height="42" viewBox="0 0 30 42"><path d="M15 2 C15 2 3 20 3 28 a12 12 0 0 0 24 0 C27 20 15 2 15 2Z" fill="#fff"/></svg>
  </div></div>
  <div class="domain-name">WATER</div>
  <div class="domain-text">toque penatibus et magnis dis par-<br>turient montes nascetur</div>
</div>
<div class="abs domain" style="left:490px;top:784px">
  <div class="domain-ring"><div class="domain-disc" style="background:var(--green)">
    <svg width="48" height="48" viewBox="0 0 48 48" fill="#fff"><circle cx="24" cy="24" r="4"/><ellipse cx="24" cy="12" rx="7" ry="9"/><ellipse cx="24" cy="36" rx="7" ry="9"/><ellipse cx="12" cy="24" rx="9" ry="7"/><ellipse cx="36" cy="24" rx="9" ry="7"/></svg>
  </div></div>
  <div class="domain-name">AIR</div>
  <div class="domain-text">toque penatibus et magnis dis par-<br>turient montes nascetur</div>
</div>
<div class="abs domain" style="left:758px;top:784px">
  <div class="domain-ring"><div class="domain-disc" style="background:var(--orange)">
    <svg width="30" height="44" viewBox="0 0 30 44"><path d="M15 2 C20 12 27 18 27 29 a12 12 0 0 1 -24 0 C3 21 9 16 11 10 C13 16 15 18 15 2Z" fill="#fff"/><path d="M15 24 C18 29 20 31 20 35 a5 5 0 0 1 -10 0 C10 31 13 29 15 24Z" fill="var(--orange)"/></svg>
  </div></div>
  <div class="domain-name">FUEL</div>
  <div class="domain-text">toque penatibus et magnis dis par-<br>turient montes nascetur</div>
</div>

<div class="abs section-rule"></div>

<div class="abs ao-text">
  <h2>ADVANCED OXIDATION</h2>
  <p>Advanced Oxidation refers to a variety of techniques employing the Hydroxyl Radical, an energetic, highly reactive cousin of the water molecule:</p>
  <ul class="ao-list">
    <li><span class="tick"><svg width="8" height="8" viewBox="0 0 8 8"><path d="M1 4 L3 6 L7 1.5" stroke="#fff" stroke-width="1.5" fill="none"/></svg></span>To add oxygen to inorganic molecules</li>
    <li><span class="tick"><svg width="8" height="8" viewBox="0 0 8 8"><path d="M1 4 L3 6 L7 1.5" stroke="#fff" stroke-width="1.5" fill="none"/></svg></span>To remove hydrogen from organic molecules</li>
  </ul>
  <p>These transformations convert important industrial contaminants<br>into reactive forms that can be captured or that disintegrate into<br>harmless end products.</p>
</div>
<div class="abs ao-visual" role="img" aria-label="Glossy blue molecular model of linked spheres on a pale blue background"></div>

<article class="abs tile tile-fuel" role="img" aria-label="Green-toned refinery towers and pipework">
  <svg class="tile-icon" viewBox="0 0 60 70"><rect x="12" y="8" width="36" height="58" rx="4" fill="#fff"/><rect x="12" y="24" width="36" height="3" fill="#5bb045"/><rect x="12" y="48" width="36" height="3" fill="#5bb045"/><path d="M30 30 C30 30 24 38 24 41 a6 6 0 0 0 12 0 C36 38 30 30 30 30Z" fill="#5bb045"/></svg>
  <h3>Fuel Oil Desulfurization</h3>
  <p>Our proprietary low temperature and pressure advanced oxidation cata-<br>lytic process reliably removes sulfur from diesel transportation</p>
  <span class="read-more">READ MORE</span>
</article>
<article class="abs tile tile-voc" role="img" aria-label="Orange-toned worker in protective suit handling chemical barrels">
  <svg class="tile-icon" viewBox="0 0 60 70" fill="#fff"><rect x="8" y="10" width="20" height="26" rx="3"/><rect x="32" y="10" width="20" height="26" rx="3"/><rect x="8" y="40" width="20" height="26" rx="3"/><rect x="32" y="40" width="20" height="26" rx="3"/></svg>
  <h3>Volatile Organic Compunds (VOC)</h3>
  <p>Alkanes, alkenes, halogenated hydrocarbons, aromatic hydrocarbons,<br>esters, aldehydes, polycyclic aromatic hydrocarbons.</p>
  <span class="read-more">READ MORE</span>
</article>
<article class="abs tile tile-flue" role="img" aria-label="Blue-toned industrial plant with smoking chimneys">
  <svg class="tile-icon" viewBox="0 0 60 70" fill="#fff"><circle cx="38" cy="10" r="6"/><circle cx="48" cy="8" r="5"/><rect x="14" y="14" width="8" height="24"/><rect x="26" y="20" width="8" height="18"/><rect x="6" y="38" width="48" height="28"/><rect x="12" y="46" width="8" height="4" fill="#2b9fdc"/><rect x="26" y="46" width="8" height="4" fill="#2b9fdc"/><rect x="40" y="46" width="8" height="4" fill="#2b9fdc"/></svg>
  <h3>Flue Gas Scrubbing</h3>
  <p>Desulfurization and denitrification using our proprietary flue gas advanced<br>oxidation catalytic process (FGAOC). Sulfur and nitrogen</p>
  <span class="read-more">READ MORE</span>
</article>
<article class="abs tile tile-water" role="img" aria-label="Dark blue-toned wastewater treatment basins">
  <svg class="tile-icon" viewBox="0 0 60 70" fill="none" stroke="#fff" stroke-width="3"><path d="M30 4 C30 4 20 20 20 27 a10 10 0 0 0 20 0 C40 20 30 4 30 4Z" fill="#fff"/><path d="M6 46 q6 -5 12 0 t12 0 t12 0 t12 0"/><path d="M6 55 q6 -5 12 0 t12 0 t12 0 t12 0"/><path d="M6 64 q6 -5 12 0 t12 0 t12 0 t12 0"/></svg>
  <h3>Wastewater Treatment</h3>
  <p>Photoelectrocatalysed (PEC) anodic oxidation removes soluble organics.<br>Novel anode design using our proprietary nano-carbon</p>
  <span class="read-more">READ MORE</span>
</article>
<div class="abs solution-badge">OUR<br>SOLUTION</div>

<h2 class="abs partners-title center" style="font-weight:400">OUR PARTNERS</h2>
<div class="abs partner" style="left:227px;top:2136px">
  <div class="partner-mark"><span class="partner-name">Velqua Systems</span></div>
  <div class="partner-role">OUR SALES PARTNER<br>IN CHINA</div>
</div>
<div class="abs partner" style="left:408px;top:2136px">
  <div class="partner-mark"><svg width="96" height="96"><rect x="12" y="12" width="72" height="72" rx="6" fill="#d8422a"/></svg></div>
  <div class="partner-role">OUR CONSTRUCTION<br>PARTNER IN CHINA</div>
</div>
<div class="abs partner" style="left:612px;top:2136px">
  <div class="partner-mark"><svg width="96" height="96"><circle cx="48" cy="48" r="44" fill="#2c4f8f"/></svg></div>
  <div class="partner-role">OUR TECHNOLOGY<br>PARTNER IN CHINA</div>
</div>
<div class="abs partner" style="left:773px;top:2136px">
  <div class="partner-mark"><svg width="96" height="96"><circle cx="48" cy="48" r="44" fill="#b3262c"/></svg></div>
  <div class="partner-role">OUR TECHNOLOGY<br>PARTNER IN CHINA</div>
</div>

<footer class="abs contact">
</footer>
<div class="abs contact-map" role="img" aria-label="Faint dotted world map behind the contact form"></div>
<h2 class="abs contact-title center" style="font-weight:400">CONTACT US</h2>
<div class="abs contact-rule"></div>
<div class="abs field" style="top:2507px;height:30px">Name</div>
<div class="abs field" style="top:2544px;height:30px">Email address</div>
<div class="abs field" style="top:2584px;height:75px">Message</div>
<div class="abs send">SEND</div>
<div class="abs contact-info">
  <div>Velqua Research Corporation</div>
  <div>Northfield, U.S.A.</div>
  <div class="row"><svg width="12" height="12" viewBox="0 0 12 12"><path d="M2 1 L4.5 1 L5.5 4 L4 5 Q5 7.5 7 8 L8 6.5 L11 7.5 L11 10 Q6 11.5 2 6 Q0.5 3 2 1Z" fill="#fff"/></svg>info@velquaresearch.example</div>
  <div class="row"><svg width="12" height="12" viewBox="0 0 12 12"><rect x="1" y="2.5" width="10" height="7" fill="none" stroke="#fff" stroke-width="1.3"/><path d="M1 3 L6 7 L11 3" fill="none" stroke="#fff" stroke-width="1.3"/></svg>+1 555 014 2290</div>
</div>
<div class="abs social"><span></span><span></span><span></span><span></span></div>
<div class="abs footer-rule"></div>
<p class="abs footer-note">© 2016 Company Name &nbsp;All right reserved &nbsp;Term of Use</p>

</body>
</html>
```